Email signatures and letterhead for in-house lawyers and staff

I need Word, Outlook, and Gmail compatible letterhead and email signature block for an in-house litigation group. Simple and generic is the goal! The design must be user-modifiable for several locations and job titles. The design will work best if created in MS Word. We are an in-house group of trial lawyers, about 40 persons total, operating from nine locations, and providing services in ten US states. Letterhead will be used in header of MSWord documents. Email sig will be used in both Outlook and Gmail. The office name will be different in each of our locations, so the design has to be user-modifiable.

Industry/Entity Type

Law Firm

Font styles to use
Sans Serif

Requirements
Must have
• A fresher, more professional look than the screenshots I've posted

The screenshot with multiple attorney names in the office is most representative of the info we want included.
Nice to have
• Sylish but not overly so. Generic legal symbols might be appropriate, but can't look like tired old clip art.
Should not have
• watermarks

```html
<!DOCTYPE html>
<html lang="en">
<head>
<meta charset="utf-8">
<title>Letterhead and Email Signature</title>
<link href="https://fonts.googleapis.com/css2?family=Fira+Sans:wght@400;500;600&display=swap" rel="stylesheet">
<style>
  :root {
    --blue: #2a5bb5;
    --bronze: #a0743a;
    --bronze-dark: #5e4324;
    --ink: #2b2b2b;
    --rule: #d8b88a;
    --paper: #ffffff;
    --backdrop: #eef0f2;
  }
  * { margin: 0; padding: 0; box-sizing: border-box; }
  html, body { width: 1200px; height: 1200px; overflow: hidden; background: var(--backdrop); }
  body { position: relative; font-family: "Fira Sans", Arial, sans-serif; color: var(--ink); }

  .sheet { position: absolute; background: var(--paper); border: 1px solid #d4d7db; }
  .abs { position: absolute; }

  /* Letterhead */
  .letterhead { left: 280px; top: 30px; width: 640px; height: 828px; }
  .letterhead .office-title { left: 33px; top: 31px; font-size: 16px; color: var(--blue); font-weight: 400; }
  .brand-art { position: absolute; overflow: visible; }
  .letterhead .contact { left: 35px; top: 76px; font-size: 10px; line-height: 15px; }
  .contact .label { color: var(--bronze); display: inline-block; width: 31px; }
  .letterhead .contact-rule { left: 35px; top: 127px; width: 273px; height: 1px; background: var(--rule); }
  .letterhead .attorneys { left: 35px; top: 133px; font-size: 12px; }
  .letterhead .recipient { left: 60px; top: 222px; font-size: 11.5px; line-height: 23.4px; }
  .letterhead .body { left: 60px; top: 314px; width: 510px; font-size: 11.5px; line-height: 23.4px; }
  .letterhead .body p + p { margin-top: 23.4px; }
  .letterhead .closing { left: 65px; top: 634px; font-size: 11.5px; }
  .signature-mark { background: linear-gradient(90deg, rgba(42,91,181,.18), rgba(42,91,181,.08)); border-radius: 3px; }
  .letterhead .signature-mark { left: 62px; top: 653px; width: 202px; height: 30px; }
  .letterhead .address { left: 46px; top: 762px; font-size: 10px; line-height: 14.5px; }

  /* Email signature */
  .email-sig { left: 210px; top: 880px; width: 780px; height: 300px; }
  .email-sig .signature-mark { left: 42px; top: 23px; width: 260px; height: 38px; }
  .email-sig .role { left: 62px; top: 63px; font-size: 16px; color: var(--bronze); }
  .email-sig .details { left: 40px; top: 100px; font-size: 10.5px; line-height: 17.8px; font-weight: 500; }
  .details .key { color: var(--blue); }
  .email-sig .disclaimer { left: 35px; top: 204px; width: 500px; font-size: 6.5px; line-height: 13.6px; }
  .email-sig .disclaimer p + p { margin-top: 13.6px; }
</style>
</head>
<body>

<section class="sheet letterhead">
  <h1 class="abs office-title">Law Office Of Daniel R. Hartley</h1>
  <svg class="brand-art" width="640" height="120" viewBox="0 0 640 120" style="left:0;top:0">
    <polygon points="590,28 611,64 590,64" fill="var(--bronze-dark)"/>
    <polygon points="491,68 509,68 509,103" fill="var(--bronze-dark)"/>
    <rect x="26" y="60" width="585" height="8" rx="4" fill="var(--blue)"/>
    <rect x="509" y="28" width="81" height="75" fill="var(--bronze)" role="img" aria-label="Scales of justice emblem"/>
  </svg>
  <div class="abs contact">
    <div><span class="label">Phone</span>: 555 -010 -2222</div>
    <div><span class="label">Fax</span>: 555 -010 -3333</div>
    <div><span class="label">Email</span>: counsel@nm-legal.com</div>
  </div>
  <div class="abs contact-rule"></div>
  <div class="abs attorneys">Daniel R. Hartley | Owen L. Pratt | Clara M. Voss</div>

  <div class="abs recipient">To<br>The,<br>Director</div>
  <div class="abs body">
    <p>Lorem ipsum dolor sit amet, consectetur adipiscing elit. Integer nec odio, vulptate dictum, massa quis pretium feugiat, nisi lectus sagittis tortor, a posuere ligula. Pellen tesque aliquet nibh nec urna. In nisi neque, aliquet vel, dapibus id, aliquam molestie varius ac, mattis quis, ante. Donec facilisis tellus sed pellen tesque lorem.</p>
    <p>Curabitur sit amet erat quis risus feugiat viverra. Pellentesque augue justo, venenatis non, arcu. Nunc feugiat mi a tellus consequat imperdiet. Vestibulum orci. Curabitur dolonunc,egestas sed libero at elementum sodales neque eros volutpat. Vestibulum ante ipsum primis in faucibus orci luctus et ultrices posuere cubilia Curae; Ut sit amet orci vel mauris blandit vehicula. Nullam quis enim. Integer dignissim viverra velit. Curabitur in odio.</p>
  </div>
  <div class="abs closing">Thanking you,</div>
  <div class="abs signature-mark" role="img" aria-label="Handwritten signature of Daniel R. Hartley"></div>
  <div class="abs address">4100 Lakeside Blvd, East, Suite 257<br>Rivertown, XY 99999</div>
</section>

<section class="sheet email-sig">
  <div class="abs signature-mark" role="img" aria-label="Handwritten signature of Daniel R. Hartley"></div>
  <div class="abs role">Attorney at law</div>
  <div class="abs details">
    <div>Law Office Of Daniel R. Hartley</div>
    <div><span class="key">T :</span> 555.020.1111 | <span class="key">F :</span> 555.020.4444</div>
    <div>daniel.hartley@nm-legal.com</div>
    <div>2850 Harbor Ave. East - Suite 575, Rivertown, XY 86753</div>
  </div>
  <svg class="brand-art" width="780" height="300" viewBox="0 0 780 300" style="left:0;top:0">
    <polygon points="705,129 739,182 705,182" fill="var(--bronze-dark)"/>
    <polygon points="548,192 577,192 577,248" fill="var(--bronze-dark)"/>
    <rect x="28" y="179" width="711" height="13" rx="5" fill="var(--blue)"/>
    <rect x="577" y="129" width="128" height="119" fill="var(--bronze)" role="img" aria-label="Scales of justice emblem"/>
  </svg>
  <div class="abs disclaimer">
    <p>The information contained in this communication from the sender is confidential. It is intended solely for use by the recipient and others authorized to receive it. If you are not the recipient, you are hereby notified that any disclosure, copying, distribution, or taking action in relation to the contents of this information is strictly prohibited and may be unlawful.</p>
    <p>The Law Office of Alan T. Roarke is an unincorporated association of individual licensed attorneys employed by Northgate Mutual Insurance Group for the purpose of representing Northgate Mutual Insurance Group, its policyholders, and insureds.</p>
  </div>
</section>

</body>
</html>
```